Carwash Signage

We own and operate a 25m tunnel car wash in the uk. We are looking to upgrade our signage to include the following:-

Wash selection Board Size-1300x1300mm
Conditions 1300x1300mm
Instructions 1300x1300mm
Banner 2600x600mm
Stamp card flyer a5 double sided - 9 squares for stamping 3rd square needs to say free air freshener 9th square needs to say free vip car wash.

I have attached some notes for the details that are required to be included.

We are looking for a modern smart look more European car wash style than American car wash style. It should be bold and clear. with yellow/orange & blue/green,grey colours

The final design must be in a industry standard printable format.

UPDATED BRIEF AS DISCUSSED: We require design for 2 x window decals, flag design and 50% off voucher. Attached are rough layout drawings of what they should look like - we expect the designs to be in keeping with the previous designs colours, etc that have been carried out. We Look forward to hearing from you.

Target Market(s)

local car owners within a 15-20 mile radius

Colors
0054AA
0677BA
7BADD7
CADEEF
E8F1F8
0094D4
00A9DD
6FCCEA
C7EBF8
E9F6FB
00AB8E
00BBA5
67D7C9
C6EFE9
E9F9F6

Requirements
Must have
• must be sharp and modern European look

```html
<!DOCTYPE html>
<html lang="en">
<head>
<meta charset="UTF-8">
<title>Harbourline Carwash Banner</title>
<link rel="stylesheet" href="https://fonts.googleapis.com/css2?family=Poppins:wght@700&family=Montserrat:wght@700;800&family=Arimo:wght@700&display=swap">
<style>
  :root {
    --page-bg: #8b8b89;
    --title-ink: #0a0a0a;
    --banner-top: #1f6f96;
    --banner-bottom: #1d3e57;
    --headline-yellow: #f4b71d;
    --notice-yellow: #f0e62a;
    --white: #ffffff;
    --logo-navy: #1b2a6b;
    --logo-blue: #0677ba;
    --card-a: #2a3f8f;
    --card-b: #e0523a;
    --card-c: #2f78c4;
    --card-d: #4a86c8;
  }
  * { margin: 0; padding: 0; box-sizing: border-box; }
  html, body { width: 1200px; height: 1000px; overflow: hidden; }
  body {
    position: relative;
    background: var(--page-bg);
    font-family: "Montserrat", sans-serif;
  }
  .page-title {
    position: absolute;
    top: 212px; left: 0; width: 1200px;
    text-align: center;
    font-family: "Poppins", sans-serif;
    font-weight: 700;
    font-size: 60px;
    line-height: 76px;
    color: var(--title-ink);
  }
  .banner {
    position: absolute;
    left: 88px; top: 322px;
    width: 1025px; height: 235px;
    background: linear-gradient(to bottom, var(--banner-top), var(--banner-bottom));
    box-shadow: 0 4px 10px rgba(0,0,0,0.35);
  }
  .banner__eyebrow {
    position: absolute;
    left: 22px; top: 14px;
    font-weight: 700;
    font-size: 40px;
    line-height: 50px;
    color: var(--white);
  }
  .banner__headline {
    position: absolute;
    left: 0; top: 72px; width: 1025px;
    text-align: center;
    font-weight: 800;
    font-size: 86px;
    line-height: 104px;
    color: var(--headline-yellow);
    padding-right: 30px;
  }
  .banner__payment-note {
    position: absolute;
    left: 22px; top: 203px;
    font-family: "Arimo", sans-serif;
    font-weight: 700;
    font-size: 17px;
    line-height: 22px;
    color: var(--notice-yellow);
  }
  .banner__cards {
    position: absolute;
    left: 409px; top: 201px;
    display: flex; gap: 8px;
  }
  .banner__cards span {
    display: block;
    width: 36px; height: 25px;
    border-radius: 3px;
  }
  .banner__cards .card-1 { background: var(--card-a); }
  .banner__cards .card-2 { background: var(--card-b); }
  .banner__cards .card-3 { background: var(--card-c); }
  .banner__cards .card-4 { background: var(--card-d); }
  .banner__hours {
    position: absolute;
    left: 780px; top: 162px; width: 236px;
    text-align: center;
    font-weight: 700;
    font-size: 16px;
    line-height: 21px;
    color: var(--white);
  }
  .brand-box {
    position: absolute;
    left: 818px; top: 21px;
    width: 186px; height: 64px;
    background: var(--white);
    display: flex; align-items: center; justify-content: center; gap: 8px;
  }
  .brand-box__dot {
    width: 22px; height: 22px; border-radius: 50%;
    background: var(--logo-blue);
  }
  .brand-box__name {
    font-weight: 800;
    font-size: 17px;
    color: var(--logo-navy);
    letter-spacing: 0.5px;
  }
</style>
</head>
<body>
  <h1 class="page-title">Harbourline Carwash Banner</h1>

  <section class="banner">
    <p class="banner__eyebrow">ATTENDED</p>
    <p class="banner__headline">CAR WASH</p>

    <div class="brand-box">
      <span class="brand-box__dot"></span>
      <span class="brand-box__name">HARBOURLINE</span>
    </div>

    <p class="banner__payment-note">CASH / CARD PAYMENT ACCEPTED</p>
    <div class="banner__cards" role="img" aria-label="Accepted payment card badges">
      <span class="card-1"></span>
      <span class="card-2"></span>
      <span class="card-3"></span>
      <span class="card-4"></span>
    </div>

    <p class="banner__hours">OPENING:<br>MON - SAT 8:00 TO 18:00<br>SUN 9:00 TO 18:00</p>
  </section>
</body>
</html>
```